Website for Apartment Rental in Prague

I would like to create designs of my website focused on luxury apartment rentals in Prague, Czech Republic. I created initial mock-ups, They are all attached. I need to design homepage and subpage. The mock-ups were created by combining elements from different websites that I liked but I need you to create a design that is unique and original. The attached files a only a guidance for the structure of the website but not for the design. Try to be creative.

Apartment

```html
<!DOCTYPE html>
<html lang="en">
<head>
<meta charset="utf-8">
<title>Maison Vltava — Apartments in Prague</title>
<link href="https://fonts.googleapis.com/css2?family=Roboto:ital,wght@0,400;0,500;0,700;1,400&family=Open+Sans:wght@400;600&display=swap" rel="stylesheet">
<style>
:root{
  --accent:#a47c63;
  --accent-dark:#8c6650;
  --ink:#1f1f1f;
  --muted:#8a8a8a;
  --light:#f0f0f0;
  --section-grey:#e6e6e6;
  --footer-grey:#efefef;
  --white:#ffffff;
  --line:#dddddd;
}
*{box-sizing:border-box;margin:0;padding:0}
html,body{width:1200px;height:3030px;overflow:hidden}
body{position:relative;background:var(--white);font-family:"Open Sans",Arial,sans-serif;color:var(--ink)}
.abs{position:absolute}
h1,h2,h3,h4,.heading{font-family:"Roboto",Arial,sans-serif}

/* top bar */
.topbar{left:0;top:0;width:1200px;height:82px;background:var(--white)}
.topbar .contact{top:30px;font-size:12px;color:#555;display:flex;align-items:center;gap:10px}
.brand{left:0;width:1200px;top:24px;text-align:center;font-family:"Roboto",Arial,sans-serif;font-weight:500;font-size:20px;letter-spacing:3px;color:var(--accent-dark);text-transform:uppercase}
.follow{right:200px;top:30px;display:flex;align-items:center;gap:18px;font-size:12px;color:var(--accent)}
.follow .dot{width:12px;height:12px;border-radius:50%;background:#9a9a9a}

/* hero */
.hero{left:0;top:82px;width:1200px;height:438px;background:linear-gradient(180deg,#3c3630 0%,#5e564d 45%,#2e2a26 100%)}
.hero .nav{left:200px;top:24px;width:800px;display:flex;justify-content:space-between;font-family:"Roboto",Arial,sans-serif;font-weight:500;font-size:14px;color:var(--white)}
.hero h1{left:0;top:152px;width:1200px;text-align:center;color:var(--white);font-size:40px;font-weight:700;letter-spacing:.5px}
.arrow-btn{width:40px;height:40px;border-radius:50%;background:var(--white);display:flex;align-items:center;justify-content:center}
.booking{left:200px;top:252px;width:800px;height:48px;background:var(--white);display:flex}
.booking .field{flex:1;border-right:1px solid var(--line);display:flex;align-items:center;justify-content:space-between;padding:0 12px;font-size:11px;color:#777}
.booking .field.wide{flex:1.4}
.booking .check{width:136px;background:var(--accent);color:var(--white);font-family:"Roboto",Arial,sans-serif;font-weight:700;font-size:11px;display:flex;align-items:center;justify-content:center}
.slider-dots{left:580px;top:352px;display:flex;gap:4px}
.slider-dots span{width:9px;height:9px;border:1px solid #fff;background:rgba(255,255,255,.4)}
.slider-dots span.on{background:#fff}

/* section heading */
.rule{width:66px;height:3px;background:var(--accent);left:567px}
.section-title{left:0;width:1200px;text-align:center;font-size:23px;font-weight:700;text-transform:uppercase}
.btn{height:44px;width:156px;background:var(--accent);color:var(--white);font-family:"Roboto",Arial,sans-serif;font-weight:700;font-size:12px;display:flex;align-items:center;justify-content:center;box-shadow:0 5px 0 #5e4435;text-transform:uppercase}

.intro-text{left:200px;top:674px;width:800px;text-align:center;font-size:12px;line-height:24px;color:#333}

/* apartments */
.apartments{left:0;top:860px;width:1200px;height:910px;background:linear-gradient(135deg,#e9e9e9 0%,#dedede 50%,#e8e8e8 100%)}
.view-all{left:920px;top:134px;font-family:"Roboto",Arial,sans-serif;font-size:12px;font-weight:500;color:#333;display:flex;gap:10px;align-items:center}
.card{width:240px;height:320px;background:var(--white);box-shadow:0 3px 8px rgba(0,0,0,.18)}
.card .photo{height:166px;width:240px}
.card h3{font-size:13px;font-weight:700;line-height:18px;margin:18px 16px 6px}
.card p{font-size:10px;color:var(--muted);line-height:16px;margin:0 16px}
.card .meta{position:absolute;left:16px;right:16px;bottom:14px;border-top:1px solid #eee;padding-top:12px;display:flex;justify-content:space-between;font-family:"Roboto",Arial,sans-serif;font-style:italic;font-size:11px;color:#666}
.card .meta span{display:flex;align-items:center;gap:8px}
.details-tag{left:70px;top:68px;width:100px;height:28px;border:1px solid #fff;color:#fff;font-size:11px;display:flex;align-items:center;justify-content:center;font-family:"Roboto",Arial,sans-serif}

/* interiors */
.interiors{left:0;top:1770px;width:1200px;height:410px;background:linear-gradient(90deg,#cfc9c2 0%,#8b8580 35%,#6a625a 70%,#a9a39d 100%)}
.interiors .panel{left:200px;top:70px;width:800px;height:270px;background:var(--white);text-align:center}
.interiors h3{font-size:15px;font-weight:700;margin-top:100px}
.interiors p{font-size:11px;color:var(--muted);line-height:20px;width:720px;margin:12px auto 0}

/* gallery */
.gallery{left:0;top:2360px;width:1200px;height:380px;display:flex;gap:2px}
.gallery .tile{flex:1;height:380px}
.gallery .caption{left:30px;top:0;width:240px;height:380px;display:flex;flex-direction:column;align-items:center;justify-content:center;color:#fff;text-align:center;font-family:"Roboto",Arial,sans-serif;font-weight:700;font-size:15px;line-height:20px;background:rgba(0,0,0,.35)}
.gallery .caption .ring{width:44px;height:44px;border:2px solid #fff;border-radius:50%;margin-bottom:12px;display:flex;align-items:center;justify-content:center}

/* footer */
.footer{left:0;top:2740px;width:1200px;height:240px;background:var(--footer-grey)}
.footer h4{font-size:13px;font-weight:700;text-transform:uppercase;margin-bottom:14px}
.footer .col{top:38px;font-size:11px;color:#555}
.footer .sub{font-size:11px;color:#666;margin-bottom:14px}
.email-box{width:244px;height:40px;background:var(--white);display:flex;align-items:center;justify-content:space-between;padding:0 14px;color:#888}
.links{display:grid;grid-template-columns:130px 150px;row-gap:10px}
.contact-row{display:flex;gap:14px;align-items:flex-start;margin-bottom:14px;line-height:16px}
.bottombar{left:0;top:2980px;width:1200px;height:50px;background:var(--white);border-top:1px solid #e5e5e5}
.bottombar .copy{left:200px;top:18px;font-size:11px;color:#444}
.bottombar .social{right:200px;top:12px;display:flex;gap:6px}
.bottombar .social span{width:24px;height:24px;background:#2a2a2a}
</style>
</head>
<body>

<header class="abs topbar">
  <div class="abs contact" style="left:200px">
    <svg width="14" height="14" viewBox="0 0 24 24"><path fill="#a47c63" d="M6.6 10.8a15 15 0 0 0 6.6 6.6l2.2-2.2a1 1 0 0 1 1-.25 11.4 11.4 0 0 0 3.6.6 1 1 0 0 1 1 1V20a1 1 0 0 1-1 1A17 17 0 0 1 3 4a1 1 0 0 1 1-1h3.5a1 1 0 0 1 1 1c0 1.25.2 2.45.57 3.57a1 1 0 0 1-.25 1z"/></svg>
    +1234567891
  </div>
  <div class="abs contact" style="left:328px">
    <svg width="16" height="12" viewBox="0 0 16 12"><rect x=".5" y=".5" width="15" height="11" fill="none" stroke="#a47c63"/><path d="M.5.5 8 7 15.5.5" fill="none" stroke="#a47c63"/></svg>
    info@maisonvltava.com
  </div>
  <div class="abs brand">Maison Vltava</div>
  <div class="abs follow">Follow Us: <span class="dot"></span><span class="dot"></span><span class="dot"></span><span class="dot"></span></div>
</header>

<section class="abs hero" role="img" aria-label="Photo of a modern apartment living room with large windows overlooking Prague">
  <nav class="abs nav">
    <span>Apartments</span><span>Location</span><span>Services</span><span>Gallery</span><span>News</span><span>Exclusive Offers &amp; Tours</span><span>For Families</span><span>Contact Us</span>
  </nav>
  <h1 class="abs">BEING HOME IN PRAGUE</h1>
  <div class="abs arrow-btn" style="left:118px;top:198px"><svg width="10" height="14" viewBox="0 0 10 14"><path d="M8 1 2 7l6 6" fill="none" stroke="#222" stroke-width="2"/></svg></div>
  <div class="abs arrow-btn" style="left:1028px;top:198px"><svg width="10" height="14" viewBox="0 0 10 14"><path d="m2 1 6 6-6 6" fill="none" stroke="#222" stroke-width="2"/></svg></div>
  <form class="abs booking">
    <div class="field">Check In <svg width="14" height="14" viewBox="0 0 14 14"><rect x="1" y="2" width="12" height="11" fill="none" stroke="#a47c63"/><path d="M1 5h12" stroke="#a47c63"/></svg></div>
    <div class="field">Check Out <svg width="14" height="14" viewBox="0 0 14 14"><rect x="1" y="2" width="12" height="11" fill="none" stroke="#a47c63"/><path d="M1 5h12" stroke="#a47c63"/></svg></div>
    <div class="field">Adults <svg width="12" height="14" viewBox="0 0 12 14"><circle cx="6" cy="3.5" r="3" fill="#a47c63"/><path d="M0 14a6 6 0 0 1 12 0z" fill="#a47c63"/></svg></div>
    <div class="field">Children <svg width="12" height="14" viewBox="0 0 12 14"><circle cx="6" cy="3" r="2.5" fill="#a47c63"/><path d="M1 6h10M6 6v4M6 10l-3 4M6 10l3 4" stroke="#a47c63" stroke-width="1.6"/></svg></div>
    <div class="field">Infants <svg width="10" height="14" viewBox="0 0 10 14"><circle cx="5" cy="3" r="2.5" fill="#a47c63"/><rect x="2" y="6" width="6" height="7" rx="3" fill="#a47c63"/></svg></div>
    <div class="field wide">Promotional Code <svg width="12" height="14" viewBox="0 0 12 14"><rect x="1" y="1" width="8" height="10" fill="none" stroke="#a47c63"/><rect x="3" y="3" width="8" height="10" fill="#fff" stroke="#a47c63"/></svg></div>
    <div class="check">CHECK AVAILABILITY</div>
  </form>
  <div class="abs slider-dots"><span class="on"></span><span></span><span></span></div>
</section>

<section>
  <div class="abs rule" style="top:604px"></div>
  <h2 class="abs section-title" style="top:620px">A Diffrent Vision of Travelling</h2>
  <p class="abs intro-text">Lorem Ipsum is simply dummy text of the printing and typesetting industry. Lorem Ipsum has been the industry's standard dummy text ever since the 1500s, when an unknown printer took a galley of type and scrambled it to make a type specimen book.</p>
  <a class="abs btn" style="left:522px;top:744px">Read More</a>
</section>

<section class="abs apartments">
  <div class="abs rule" style="top:68px"></div>
  <h2 class="abs section-title" style="top:84px">Our Apartments</h2>
  <div class="abs view-all">VIEW ALL <svg width="14" height="10" viewBox="0 0 14 10"><path d="M0 5h12M8 1l4 4-4 4" fill="none" stroke="#333" stroke-width="1.5"/></svg></div>

  <article class="abs card" style="left:200px;top:164px">
    <div class="photo" role="img" aria-label="Photo of a dark modern living room" style="background:linear-gradient(160deg,#6b655e,#2f2c29)"></div>
    <div class="abs details-tag">DETAILS</div>
    <h3>Brand New Luxry Living Stunning Cntemporary Design</h3>
    <p>Lorem Ipsum is simply dummy text of the printing and typesetting industry.</p>
    <div class="meta"><span><svg width="20" height="12" viewBox="0 0 20 12"><path d="M1 0v12M19 5v7M1 8h18M1 5h18" stroke="#a47c63" stroke-width="2" fill="none"/></svg>1 Bedroom</span><span><svg width="18" height="14" viewBox="0 0 18 14"><circle cx="6" cy="4" r="3" fill="#a47c63"/><circle cx="12" cy="4" r="3" fill="#a47c63"/><path d="M0 14a6 6 0 0 1 12 0zM6 14a6 6 0 0 1 12 0z" fill="#a47c63"/></svg>4 People</span></div>
  </article>
  <article class="abs card" style="left:480px;top:164px">
    <div class="photo" role="img" aria-label="Photo of a bright kitchen and dining area" style="background:linear-gradient(160deg,#ddd6cc,#9b7a5e)"></div>
    <h3>Brand New Luxry Living Aparm-ent in the Center of Pargue</h3>
    <p>Lorem Ipsum is simply dummy text of the printing and typesetting industry.</p>
    <div class="meta"><span><svg width="20" height="12" viewBox="0 0 20 12"><path d="M1 0v12M19 5v7M1 8h18M1 5h18" stroke="#a47c63" stroke-width="2" fill="none"/></svg>1 Bedroom</span><span><svg width="18" height="14" viewBox="0 0 18 14"><circle cx="6" cy="4" r="3" fill="#a47c63"/><circle cx="12" cy="4" r="3" fill="#a47c63"/><path d="M0 14a6 6 0 0 1 12 0zM6 14a6 6 0 0 1 12 0z" fill="#a47c63"/></svg>4 People</span></div>
  </article>
  <article class="abs card" style="left:760px;top:164px">
    <div class="photo" role="img" aria-label="Photo of a white living room with sofa" style="background:linear-gradient(160deg,#efece6,#b9ada0)"></div>
    <h3>Expedition Prague Top Local Brand New Apartment</h3>
    <p>Lorem Ipsum is simply dummy text of the printing and typesetting industry.</p>
    <div class="meta"><span><svg width="20" height="12" viewBox="0 0 20 12"><path d="M1 0v12M19 5v7M1 8h18M1 5h18" stroke="#a47c63" stroke-width="2" fill="none"/></svg>1 Bedroom</span><span><svg width="18" height="14" viewBox="0 0 18 14"><circle cx="6" cy="4" r="3" fill="#a47c63"/><circle cx="12" cy="4" r="3" fill="#a47c63"/><path d="M0 14a6 6 0 0 1 12 0zM6 14a6 6 0 0 1 12 0z" fill="#a47c63"/></svg>4 People</span></div>
  </article>

  <article class="abs card" style="left:200px;top:524px">
    <div class="photo" role="img" aria-label="Photo of a living room with wooden floor" style="background:linear-gradient(170deg,#e8e6e2 0%,#b8b3ad 60%,#7a4a30 100%)"></div>
    <h3>Brand New Luxry Living Stunning Cntemporary Design</h3>
    <p>Lorem Ipsum is simply dummy text of the printing and typesetting industry.</p>
    <div class="meta"><span><svg width="20" height="12" viewBox="0 0 20 12"><path d="M1 0v12M19 5v7M1 8h18M1 5h18" stroke="#a47c63" stroke-width="2" fill="none"/></svg>1 Bedroom</span><span><svg width="18" height="14" viewBox="0 0 18 14"><circle cx="6" cy="4" r="3" fill="#a47c63"/><circle cx="12" cy="4" r="3" fill="#a47c63"/><path d="M0 14a6 6 0 0 1 12 0zM6 14a6 6 0 0 1 12 0z" fill="#a47c63"/></svg>4 People</span></div>
  </article>
  <article class="abs card" style="left:480px;top:524px">
    <div class="photo" role="img" aria-label="Photo of a grey lounge with white sofas" style="background:linear-gradient(160deg,#dcdcdc,#8e9094)"></div>
    <h3>Brand New Luxry Living Aparm-ent in the Center of Pargue</h3>
    <p>Lorem Ipsum is simply dummy text of the printing and typesetting industry.</p>
    <div class="meta"><span><svg width="20" height="12" viewBox="0 0 20 12"><path d="M1 0v12M19 5v7M1 8h18M1 5h18" stroke="#a47c63" stroke-width="2" fill="none"/></svg>1 Bedroom</span><span><svg width="18" height="14" viewBox="0 0 18 14"><circle cx="6" cy="4" r="3" fill="#a47c63"/><circle cx="12" cy="4" r="3" fill="#a47c63"/><path d="M0 14a6 6 0 0 1 12 0zM6 14a6 6 0 0 1 12 0z" fill="#a47c63"/></svg>4 People</span></div>
  </article>
  <article class="abs card" style="left:760px;top:524px">
    <div class="photo" role="img" aria-label="Photo of a cream living room with dark coffee table" style="background:linear-gradient(160deg,#f1ece2,#6d5a48)"></div>
    <h3>Expedition Prague Top Local Brand New Apartment</h3>
    <p>Lorem Ipsum is simply dummy text of the printing and typesetting industry.</p>
    <div class="meta"><span><svg width="20" height="12" viewBox="0 0 20 12"><path d="M1 0v12M19 5v7M1 8h18M1 5h18" stroke="#a47c63" stroke-width="2" fill="none"/></svg>1 Bedroom</span><span><svg width="18" height="14" viewBox="0 0 18 14"><circle cx="6" cy="4" r="3" fill="#a47c63"/><circle cx="12" cy="4" r="3" fill="#a47c63"/><path d="M0 14a6 6 0 0 1 12 0zM6 14a6 6 0 0 1 12 0z" fill="#a47c63"/></svg>4 People</span></div>
  </article>
</section>

<section class="abs interiors" role="img" aria-label="Photo of a bright interior with sofa and wooden floor">
  <div class="abs panel">
    <svg class="abs" style="left:385px;top:36px" width="30" height="44" viewBox="0 0 30 44"><path d="M15 0v6" stroke="#a47c63" stroke-width="1.5"/><path d="M4 8h22l-3 16H7z" fill="none" stroke="#a47c63" stroke-width="1.5"/><path d="M7 24v8h16v-8M9 32l-3 10M21 32l3 10" fill="none" stroke="#a47c63" stroke-width="1.5"/></svg>
    <h3>Interiors Designed By Maison Vltava</h3>
    <p>Lorem Ipsum is simply dummy text of the printing and typesetting industry. Lorem Ipsum has been the industry's standard dummy text ever since the 1500s, when an unknown printer took a galley of type and scrambled it to make a type specimen book.</p>
    <a class="abs btn" style="left:322px;top:196px">Read More</a>
  </div>
</section>

<section>
  <div class="abs rule" style="top:2252px"></div>
  <h2 class="abs section-title" style="top:2268px">Our Gallery</h2>
  <div class="abs gallery">
    <div class="tile" role="img" aria-label="Photo of an entrance hall with plant" style="background:linear-gradient(180deg,#4a3b2f,#8a6040)"></div>
    <div class="tile" role="img" aria-label="Photo of a modern kitchen with bar stools" style="background:linear-gradient(180deg,#d8d6d2,#6a5446)"></div>
    <div class="tile" role="img" aria-label="Photo of a hallway with chandelier and mirror" style="background:linear-gradient(180deg,#e2ddd6,#9a8a7a)"></div>
    <div class="tile" role="img" aria-label="Photo of a dining room with pendant lights" style="background:linear-gradient(180deg,#b9a79a,#5a3424)"></div>
    <div class="abs caption">
      <div class="ring"><svg width="18" height="18" viewBox="0 0 18 18"><path d="M7 11l4-4M6 9 4 11a2.8 2.8 0 0 0 4 4l2-2M12 9l2-2a2.8 2.8 0 0 0-4-4L8 5" fill="none" stroke="#fff" stroke-width="1.8"/></svg></div>
      Brand New Luxry Living<br>StunningCntemporary Design
    </div>
    <svg class="abs" style="left:0;top:172px" width="24" height="32" viewBox="0 0 24 32"><rect width="24" height="32" fill="rgba(0,0,0,.4)"/><path d="M16 10l-6 6 6 6" fill="none" stroke="#fff" stroke-width="2"/></svg>
    <svg class="abs" style="left:1176px;top:172px" width="24" height="32" viewBox="0 0 24 32"><rect width="24" height="32" fill="rgba(0,0,0,.4)"/><path d="M8 10l6 6-6 6" fill="none" stroke="#fff" stroke-width="2"/></svg>
  </div>
</section>

<footer class="abs footer">
  <div class="abs col" style="left:200px">
    <h4>Stay In Touch</h4>
    <p class="sub">Sign up here to receive interesting updates</p>
    <div class="email-box">Email Address <svg width="18" height="16" viewBox="0 0 18 16"><path d="M0 8 18 0 14 16 9 10z" fill="#222"/></svg></div>
  </div>
  <div class="abs col" style="left:516px">
    <h4>Quick Links</h4>
    <div class="links"><span>Apartments</span><span>News</span><span>Location</span><span>Exclusive Offers &amp; Tours</span><span>Services</span><span>For Families</span><span>Gallery</span><span>Contact Us</span></div>
  </div>
  <div class="abs col" style="left:850px">
    <h4>Contact Us</h4>
    <div class="contact-row"><svg width="14" height="14" viewBox="0 0 24 24"><path fill="#999" d="M6.6 10.8a15 15 0 0 0 6.6 6.6l2.2-2.2a1 1 0 0 1 1-.25 11.4 11.4 0 0 0 3.6.6 1 1 0 0 1 1 1V20a1 1 0 0 1-1 1A17 17 0 0 1 3 4a1 1 0 0 1 1-1h3.5a1 1 0 0 1 1 1c0 1.25.2 2.45.57 3.57a1 1 0 0 1-.25 1z"/></svg>+1234567891</div>
    <div class="contact-row"><svg width="14" height="16" viewBox="0 0 14 16"><path d="M7 0a6 6 0 0 1 6 6c0 4-6 10-6 10S1 10 1 6a6 6 0 0 1 6-6z" fill="#999"/><circle cx="7" cy="6" r="2" fill="#efefef"/></svg>Lorem Ipsum is simply<br>of the printing</div>
    <div class="contact-row"><svg width="14" height="11" viewBox="0 0 16 12"><rect x=".5" y=".5" width="15" height="11" fill="none" stroke="#999"/><path d="M.5.5 8 7 15.5.5" fill="none" stroke="#999"/></svg>info@maisonvltava.com</div>
  </div>
</footer>

<div class="abs bottombar">
  <p class="abs copy">© Copyright 2017 maisonvltava.com. All Rights Reserved.</p>
  <div class="abs social"><span></span><span></span><span></span><span></span></div>
</div>

</body>
</html>
```